Webdesign für Kleingruppenreisen in die Südsteiermark
Zielgruppe
Wir sind ein Start-Up Unternehmen, das als Kleingruppenreisen in die Südsteiermark veranstaltet; der Schwerpunkt liegt auf dem Kulinarischen. Zielgruppe sind Geschäftsleute, die diese Kurzreisen (Do-So) für Marketingzwecke oder als Mitarbeiterbonus (oder auch privat) nutzen möchten.
Aufgabenstellung
Die Homepage soll eine Online-Shop Möglichkeit bieten, in der die Reise (bisher gibt es nur einen Ablauf) gebucht werden kann. Optisch sollte sie sich an das bereits von Ihnen erstellte Logo anlehnen und möglichst ansprechende Fotos von der Südsteiermark, Graz, Leoben usw. enthalten. (Siehe die beiden Flyer und das Logo)
Wir haben inzwischen Bildfreigaben von Haldauer und dem Tourismusverband Kellwinden erhalten und können auch eigene Bilder zur Verfügung stellen. Bitte kontaktieren Sie uns dafür, wenn nötig.

```html
<!DOCTYPE html>
<html lang="de">
<head>
<meta charset="utf-8">
<title>Kostbar Reisen – Reisen für Feinschmecker in die Steiermark</title>
<link href="https://fonts.googleapis.com/css2?family=Cabin:ital,wght@1,500;1,700&family=Lato:wght@400;700&display=swap" rel="stylesheet">
<style>
:root{
  --cream:#fdf3ea;
  --white:#ffffff;
  --ink:#333333;
  --text:#3d3d3d;
  --green:#5aa86b;
  --teal:#7ecfd4;
  --orange:#ffc885;
  --red:#d2232a;
  --brand-red:#b5261e;
  --line:#8c8c8c;
}
*{box-sizing:border-box;margin:0;padding:0}
html,body{width:716px;height:1200px;overflow:hidden}
body{background:var(--white);font-family:"Lato",sans-serif;color:var(--text);position:relative}

.site-header{position:absolute;left:0;top:0;width:716px;height:113px;background:var(--cream)}
.main-nav a{position:absolute;top:89px;font-size:9px;color:var(--ink);text-decoration:none}
.brand{position:absolute;left:282px;top:48px;width:160px;display:flex;align-items:center;gap:6px}
.brand-dot{width:12px;height:12px;border-radius:50%;background:var(--brand-red);flex:none}
.brand-name{font-family:"Lato",sans-serif;font-weight:700;font-size:19px;color:var(--brand-red);white-space:nowrap}
.header-rule{position:absolute;left:0;top:113px;width:716px;height:6px;background:linear-gradient(#b5b5b5,#e6e6e6)}

.photo{position:absolute;left:0;width:716px}
.photo-hills{top:119px;height:268px;background:linear-gradient(180deg,#a9cde8 0%,#d8e6ee 40%,#8aa170 58%,#4f7a2c 78%,#6f9b2a 100%)}
.photo-wine{top:577px;height:268px;background:linear-gradient(180deg,#8a7a68 0%,#5f86a8 25%,#8fae7a 50%,#6d9640 75%,#b58d4a 100%)}

.teaser{position:absolute;left:54px;width:272px;height:112px;background:rgba(255,255,255,.55);box-shadow:2px 2px 3px rgba(0,0,0,.2);text-align:center}
.teaser h2{font-family:"Cabin",sans-serif;font-style:italic;font-weight:700;font-size:22px;line-height:28px;color:var(--ink);margin-top:9px}
.teaser .btn{position:absolute;top:70px;height:31px;border-radius:8px;background:var(--teal);color:var(--white);font-family:"Cabin",sans-serif;font-style:italic;font-weight:500;font-size:15px;line-height:31px;text-decoration:none}
.teaser-a{top:175px}
.teaser-b{top:656px;background:rgba(200,200,200,.45)}

.card{position:absolute;width:148px;height:163px;background:var(--cream);box-shadow:1px 1px 2px rgba(0,0,0,.25);font-size:7.7px;line-height:13px}
.card .icon{position:absolute;left:56px;top:6px;width:36px;height:36px;border-radius:50%;background:var(--white);box-shadow:0 1px 2px rgba(0,0,0,.25);display:flex;align-items:center;justify-content:center}
.card .body{position:absolute;top:48px;left:6px;right:4px}
.card p+p{margin-top:3px}
.card ul{list-style:none}
.card li{display:flex;align-items:center;gap:4px;height:17px}

.site-footer{position:absolute;left:0;top:1045px;width:716px;height:155px;background:var(--cream);border-top:2px solid var(--line)}
.newsletter{position:absolute;left:98px;top:11px;width:520px;height:32px;background:var(--orange);border-radius:4px}
.newsletter .field{position:absolute;left:6px;top:4px;width:138px;height:23px;background:var(--white);border:1px solid #ccc;display:flex}
.newsletter .field .ico{width:30px;border-right:1px solid #ccc;display:flex;align-items:center;justify-content:center}
.newsletter .field span{font-size:6.5px;color:#999;line-height:21px;padding-left:14px}
.newsletter h3{position:absolute;left:172px;top:4px;font-size:11px;font-weight:700;color:var(--white)}
.newsletter small{position:absolute;left:172px;top:19px;font-size:6px;color:var(--white)}
.foot-col{position:absolute;top:58px;font-size:8.4px;line-height:13px;color:var(--ink)}
.foot-col h4{color:var(--red);font-size:8.4px;font-weight:700;margin-bottom:3px}
</style>
</head>
<body>

<header class="site-header">
  <nav class="main-nav">
    <a href="#" style="left:143px">Start</a>
    <a href="#" style="left:197px">Reise buchen</a>
    <a href="#" style="left:484px">Kontakt</a>
    <a href="#" style="left:550px">Impressum</a>
  </nav>
  <div class="brand"><span class="brand-dot"></span><span class="brand-name">Kostbar Reisen</span></div>
</header>
<div class="header-rule"></div>

<section class="photo photo-hills" role="img" aria-label="Weinberge der Südsteiermark mit Klapotetz vor Hügellandschaft"></section>
<div class="teaser teaser-a">
  <h2>Haben Sie Geschmack<br>am Besonderen?</h2>
  <a class="btn" href="#" style="left:71px;width:130px">Reise buchen</a>
</div>

<article class="card" style="left:98px;top:402px">
  <div class="icon"><svg width="22" height="22" viewBox="0 0 22 22" fill="#5aa86b"><path d="M3 8h7c0 3-1.5 4.5-3 4.7V17h2v1.5H4V17h2v-4.3C4.5 12.5 3 11 3 8z"/><rect x="14" y="2" width="2" height="5"/><path d="M13 8h4c1 1 1 2 1 3v8h-6v-8c0-1 0-2 1-3z"/></svg></div>
  <div class="body" style="left:13px">
    <p>Lieben Sie...</p>
    <ul>
      <li><svg width="6" height="8" viewBox="0 0 6 8"><path d="M3 0a3 3 0 0 1 3 3c0 2-3 5-3 5S0 5 0 3a3 3 0 0 1 3-3z" fill="#5aa86b"/><circle cx="3" cy="3" r="1" fill="#fdf3ea"/></svg>gutes Essen?</li>
      <li><svg width="6" height="8" viewBox="0 0 6 8"><path d="M3 0a3 3 0 0 1 3 3c0 2-3 5-3 5S0 5 0 3a3 3 0 0 1 3-3z" fill="#5aa86b"/><circle cx="3" cy="3" r="1" fill="#fdf3ea"/></svg>hervorragendes Bier?</li>
      <li><svg width="6" height="8" viewBox="0 0 6 8"><path d="M3 0a3 3 0 0 1 3 3c0 2-3 5-3 5S0 5 0 3a3 3 0 0 1 3-3z" fill="#5aa86b"/><circle cx="3" cy="3" r="1" fill="#fdf3ea"/></svg>exquisiten Wein?</li>
      <li><svg width="6" height="8" viewBox="0 0 6 8"><path d="M3 0a3 3 0 0 1 3 3c0 2-3 5-3 5S0 5 0 3a3 3 0 0 1 3-3z" fill="#5aa86b"/><circle cx="3" cy="3" r="1" fill="#fdf3ea"/></svg>kulinarische Spezialitäten?</li>
      <li><svg width="6" height="8" viewBox="0 0 6 8"><path d="M3 0a3 3 0 0 1 3 3c0 2-3 5-3 5S0 5 0 3a3 3 0 0 1 3-3z" fill="#5aa86b"/><circle cx="3" cy="3" r="1" fill="#fdf3ea"/></svg>und gastfreundliche Menschen?</li>
      <li><svg width="6" height="8" viewBox="0 0 6 8"><path d="M3 0a3 3 0 0 1 3 3c0 2-3 5-3 5S0 5 0 3a3 3 0 0 1 3-3z" fill="#5aa86b"/><circle cx="3" cy="3" r="1" fill="#fdf3ea"/></svg>wunderschöne Landschaften?</li>
    </ul>
  </div>
</article>
<article class="card" style="left:284px;top:402px">
  <div class="icon"><svg width="24" height="20" viewBox="0 0 24 20" fill="#5aa86b"><path d="M12 2c3 3 3 8 0 12-3-4-3-9 0-12z"/><path d="M5 5c4 1 6 5 6 10-4-1-6-5-6-10z"/><path d="M19 5c-4 1-6 5-6 10 4-1 6-5 6-10z"/><path d="M1 11c3 0 6 2 9 5H4c-2-1-3-3-3-5zM23 11c-3 0-6 2-9 5h6c2-1 3-3 3-5z"/></svg></div>
  <div class="body"><p>Wir glauben, dass unsere Reisen hervorragende Möglichkeiten zum Entspannen und Genießen bieten und sich deshalb besonders gut als „Schmankerl“ für umsatzstarke Kunden, erfolgreiche Mitarbeiter oder einfach für Sie selbst und Ihre Freunde eignen.</p></div>
</article>
<article class="card" style="left:471px;top:402px">
  <div class="icon"><svg width="26" height="16" viewBox="0 0 26 16" fill="#5aa86b"><path d="M1 4l3 0 3 3h5L8 0h3l7 7h5c2 0 3 1 3 1.5S25 10 23 10h-5l-7 6H8l4-6H7l-3 3H1l2-4.5z"/></svg></div>
  <div class="body"><p>Lassen Sie das hektische Berlin und das flache Land für ein paar Tage hinter sich!<br>Die südlichen Ausläufer der Alpen und die sogenannte „steirische Toskana“ sind nur 90 Minuten Direktflug entfernt.</p></div>
</article>

<section class="photo photo-wine" role="img" aria-label="Weißwein wird vor Landschaftskulisse in zwei Gläser geschenkt"></section>
<div class="teaser teaser-b">
  <h2>Sind Sie auf den<br>Geschmack gekommen?</h2>
  <a class="btn" href="#" style="left:58px;width:156px">kontaktieren Sie uns</a>
</div>

<article class="card" style="left:98px;top:861px">
  <div class="icon"><svg width="20" height="22" viewBox="0 0 20 22" fill="#5aa86b"><rect x="6" y="2" width="2" height="18"/><path d="M8 2l10 4-10 5z"/><rect x="3" y="19" width="8" height="2" rx="1"/></svg></div>
  <div class="body"><p>Lernen Sie Leoben, die Hauptstadt des Haldauer-Bieres kennen und erfahren Sie im Braumuseum Haldau die Geschichte dieses weltbekannten Gebräus.</p></div>
</article>
<article class="card" style="left:284px;top:861px">
  <div class="icon"><svg width="24" height="24" viewBox="0 0 24 24" fill="#5aa86b"><circle cx="12" cy="12" r="6"/><path d="M12 0l2 4h-4zM12 24l-2-4h4zM0 12l4-2v4zM24 12l-4 2v-4zM3.5 3.5l4.5 1.5-3 3zM20.5 20.5l-4.5-1.5 3-3zM20.5 3.5l-1.5 4.5-3-3zM3.5 20.5l1.5-4.5 3 3z"/></svg></div>
  <div class="body"><p>Entdecken Sie Graz, die abwechslungs-reiche Landeshauptstadt und Kultur-hauptstadt 2003, mit ihren vielfältigen kulturellen Angeboten, den charmanten Gassen und atemberaubenden Ausblicken.</p><p>Genießen Sie die südlichere Sonne und kosten Sie die ausgezeichneten Weine der Winzer in der Buschenschank.</p></div>
</article>
<article class="card" style="left:471px;top:861px">
  <div class="icon"><svg width="24" height="18" viewBox="0 0 24 18" fill="#5aa86b"><rect x="3" y="0" width="18" height="7" rx="1"/><rect x="6" y="2" width="12" height="4" fill="#fff"/><rect x="0" y="8" width="24" height="6" rx="1"/><rect x="0" y="15" width="24" height="3"/></svg></div>
  <div class="body"><p>Während unser Exklusiv Transfer Sie zu den Sehenswürdigkeiten bringt, lüftet unser steirischer Reiseleiter für Sie die Geheimnisse seines Heimatlandes, des „grünen Herzens Österreichs“ und führt Sie in erstklassige Restaurants.</p><p>Sie wohnen in ausgesuchten Hotels in zentraler Lage.</p></div>
</article>

<footer class="site-footer">
  <div class="newsletter">
    <div class="field">
      <div class="ico"><svg width="17" height="11" viewBox="0 0 17 11"><rect x=".5" y=".5" width="16" height="10" fill="#ffc885" stroke="#f39a2b"/><path d="M.5 .5l8 6 8-6M.5 10.5l6-5M16.5 10.5l-6-5" fill="none" stroke="#f39a2b"/></svg></div>
      <span>Ihre E-Mail Adresse</span>
    </div>
    <h3>Newsletter</h3>
    <small>Abonnieren Sie unseren kostenlosen Newsletter und verpasse keine Neuigkeiten</small>
  </div>
  <div class="foot-col" style="left:98px">
    <h4>Telefon</h4>
    <p>XXXXXXXXXXX<br>Montag bis Freitag<br>von XX bis XX Uhr</p>
  </div>
  <div class="foot-col" style="left:268px">
    <h4>Service</h4>
    <p>Kontakt<br>&nbsp;Zahlungsbedingungen<br>AGB<br>Widerrufsrecht<br>Widerrufsformular<br>Partnerprogramm</p>
  </div>
  <div class="foot-col" style="left:446px">
    <h4>Informationen</h4>
    <p>Über uns<br>Datenschutz<br>Impressum<br>Newsletter</p>
  </div>
</footer>

</body>
</html>
```